BOLD & MINIMALIST DESIGN NEEDED

We want a very bold but minimalistic business card design that is impactful and utilizes both sides of the business card. Our current logo is included for your use.

We want bold fonts and good use of negative space. We don't want the logo to overpower the design.

Target Market(s)

Professionals who are building new commercial buildings.

Industry/Entity Type

Construction

Contact Information for Business Card

Name, Title, email, office phone, cell phone, website

Font styles to use
Serif
Sans Serif

Requirements
Must have
• Bold design!

```html
<!DOCTYPE html>
<html lang="en">
<head>
<meta charset="utf-8">
<title>Ridgeline Design + Build — Business Card</title>
<link rel="stylesheet" href="https://fonts.googleapis.com/css2?family=Poppins:wght@400;500;800&family=PT+Sans:wght@700&display=swap">
<style>
  :root {
    --stage: #b7b7b7;
    --green: #86c42b;
    --green-deep: #7cbf26;
    --green-light: #b3da80;
    --green-pale: #c9e5a4;
    --ink: #0a0b0d;
    --paper: #ffffff;
    --rule: #6c6c6c;
  }
  * { box-sizing: border-box; margin: 0; padding: 0; }
  html, body { width: 1200px; height: 1200px; overflow: hidden; }
  body {
    background: var(--stage);
    font-family: "Poppins", sans-serif;
    position: relative;
  }
  .card {
    position: absolute;
    top: 303px;
    height: 594px;
    overflow: hidden;
  }

  /* Front */
  .card--front {
    left: 201px;
    width: 368px;
    background: linear-gradient(200deg, var(--green) 0%, var(--green-light) 55%, var(--green-pale) 100%);
  }
  .brand {
    position: absolute;
    left: 0; right: 0;
    text-align: center;
    color: var(--ink);
    font-family: "Poppins", sans-serif;
    font-weight: 800;
    line-height: 1;
  }
  .brand__name { display: block; letter-spacing: 0.5px; }
  .brand__tag { display: block; letter-spacing: 0.32em; margin-top: 7px; }
  .card--front .brand { top: 112px; }
  .card--front .brand__name { font-size: 42px; }
  .card--front .brand__tag { font-size: 15px; }
  .front__mark {
    position: absolute;
    left: 0; right: 0; bottom: 0;
    height: 326px;
    background: linear-gradient(90deg, var(--ink) 0%, var(--ink) 50%, var(--green-light) 50%, var(--green-deep) 100%);
  }

  /* Back */
  .card--back {
    left: 599px;
    width: 364px;
    background: var(--paper);
  }
  .card--back .brand { top: 168px; }
  .card--back .brand__name { font-size: 40px; }
  .card--back .brand__tag { font-size: 14px; }
  .back__horizon {
    position: absolute;
    left: 0; right: 0;
    top: 293px;
    height: 52px;
    background: linear-gradient(180deg, rgba(179,218,128,0) 0%, var(--green-light) 55%, var(--green-deep) 100%);
  }
  .back__panel {
    position: absolute;
    left: 0; right: 0; bottom: 0;
    top: 345px;
    background: var(--ink);
    color: var(--paper);
    text-align: center;
  }
  .person__name {
    margin-top: 30px;
    font-family: "PT Sans", sans-serif;
    font-weight: 700;
    font-size: 24px;
    letter-spacing: 0.5px;
    line-height: 1;
  }
  .person__title {
    margin-top: 7px;
    font-size: 14.5px;
    font-weight: 500;
    color: var(--green);
    letter-spacing: 0.3px;
    line-height: 1;
  }
  .icon-row {
    margin-top: 19px;
    display: flex;
    justify-content: center;
    align-items: center;
    gap: 4px;
  }
  .icon-row__rule {
    width: 52px;
    height: 1px;
    background: var(--rule);
    margin: 0 4px;
  }
  .icon {
    width: 25px; height: 25px;
    border-radius: 4px;
    background: var(--green);
    display: flex; align-items: center; justify-content: center;
  }
  .icon svg { width: 15px; height: 15px; }
  .contact {
    margin-top: 13px;
    list-style: none;
    font-size: 17px;
    line-height: 22px;
    font-weight: 400;
  }
  .contact__accent { color: var(--green); }
</style>
</head>
<body>

  <section class="card card--front" aria-label="Card front">
    <h1 class="brand">
      <span class="brand__name">RIDGELINE</span>
      <span class="brand__tag">DESIGN + BUILD</span>
    </h1>
    <div class="front__mark" role="img" aria-label="Large company building mark in black and green"></div>
  </section>

  <section class="card card--back" aria-label="Card back">
    <div class="brand">
      <span class="brand__name">RIDGELINE</span>
      <span class="brand__tag">DESIGN + BUILD</span>
    </div>
    <div class="back__horizon" role="img" aria-label="Green horizon band with small building mark"></div>

    <div class="back__panel">
      <p class="person__name">MARCUS HALE</p>
      <p class="person__title">MANAGING DIRECTOR</p>

      <div class="icon-row">
        <span class="icon-row__rule"></span>
        <span class="icon" aria-label="Office phone">
          <svg viewBox="0 0 16 16" fill="#fff"><path d="M2 6c0-2 2.5-3 6-3s6 1 6 3v1h-3V5.5H5V7H2z"/><path d="M4 8h8l1.5 5h-11z"/></svg>
        </span>
        <span class="icon" aria-label="Mobile phone">
          <svg viewBox="0 0 16 16" fill="none" stroke="#fff" stroke-width="1.6"><rect x="4.5" y="1.5" width="7" height="13" rx="1.2"/><line x1="7" y1="12" x2="9" y2="12"/></svg>
        </span>
        <span class="icon" aria-label="Email">
          <svg viewBox="0 0 16 16" fill="none" stroke="#fff" stroke-width="1.4"><rect x="1.5" y="3.5" width="13" height="9"/><path d="M1.5 3.5l6.5 5 6.5-5M1.5 12.5l5-4.5M14.5 12.5l-5-4.5"/></svg>
        </span>
        <span class="icon" aria-label="Website">
          <svg viewBox="0 0 16 16" fill="none" stroke="#fff" stroke-width="1.4"><circle cx="8" cy="8" r="6.3"/><ellipse cx="8" cy="8" rx="2.8" ry="6.3"/><line x1="1.7" y1="8" x2="14.3" y2="8"/></svg>
        </span>
        <span class="icon-row__rule"></span>
      </div>

      <ul class="contact">
        <li>044-555 010 200</li>
        <li>044-555 010 201</li>
        <li>info@ridgelinebuild.com</li>
        <li>www.<span class="contact__accent">ridgelinebuild</span>.com</li>
      </ul>
    </div>
  </section>

</body>
</html>
```